Pool Screen Enclosure Building a Career Boot Camp!

Looking to Host a Boot Camp for people looking for a career or looking to change careers. We Design, Manufacture and Install Custom Pool Screen Enclosures. We have a training program to allow Non Experienced motivated people the chance at a great career that will provide a great living for them and their family. This will be a paid boot camp, week long, we provide all the initial training for them to make a transition into our business. This will be 5 days of training with a guaranteed job to start the following Monday.... This is good for both someone with no construction experience or someone with construction experience that wants to upgrade their current job.
Paid Boot Camp
transition to a full time job with great pay
Benefits include Health Insurance, Dental and Vision, 401K, we provide the tools and training.

```html
<!DOCTYPE html>
<html lang="en">
<head>
<meta charset="utf-8">
<title>Career Boot Camp Flyer</title>
<link rel="stylesheet" href="https://fonts.googleapis.com/css2?family=Montserrat:wght@700;800;900&family=Open+Sans:wght@400;600&family=Poppins:wght@500;600&display=swap">
<style>
  :root{
    --sky-top:#d8dee8;
    --sky-bottom:#c3cbd7;
    --yellow:#f5bd0a;
    --green:#1f9a3f;
    --green-light:#5bbb4a;
    --ink:#161616;
    --footer:#1c1c1c;
    --panel:#f1f1f1;
    --paper:#ebebeb;
    --white:#ffffff;
    --page:#e9e9e9;
  }
  *{box-sizing:border-box;margin:0;padding:0}
  html,body{width:990px;height:1200px;overflow:hidden;background:var(--page)}
  .flyer{
    position:absolute;left:31px;top:0;width:1183px;height:1531px;
    transform:scale(0.7838);transform-origin:top left;
    background:var(--paper);overflow:hidden;
    font-family:"Open Sans",Arial,sans-serif;color:var(--ink);
  }
  .hero{position:absolute;left:0;top:0;width:1183px;height:600px;
    background:linear-gradient(180deg,var(--sky-top),var(--sky-bottom))}
  .worker-photo{position:absolute;left:690px;top:30px;width:450px;height:570px;
    background:linear-gradient(180deg,#cfd5de 0%,#d9c6bb 35%,#e3e3e6 60%,#d59a6c 100%)}
  .headline{position:absolute;left:0;top:0;width:700px;text-align:center;
    font-family:"Montserrat",Arial,sans-serif;font-weight:900;line-height:1}
  .headline .lead{position:absolute;font-family:"Poppins",Arial,sans-serif;font-weight:600;
    font-size:52px;color:var(--ink)}
  .headline .big{position:absolute;letter-spacing:-3px;text-shadow:4px 5px 0 var(--ink)}
  .lead-1{left:202px;top:80px}
  .big-career{left:96px;top:115px;font-size:128px;color:var(--yellow)}
  .lead-2{left:248px;top:234px}
  .big-boot{left:188px;top:262px;font-size:132px;color:var(--green)}
  .big-camp{left:96px;top:372px;font-size:132px;color:var(--green)}
  .divider{position:absolute;left:0;top:592px;width:1183px;height:10px;background:var(--white)}
  .band{position:absolute;left:0;top:600px;width:1183px;height:306px;background:var(--yellow)}
  .thumb{position:absolute;top:514px;width:305px;height:187px;background:var(--white);
    padding:8px;box-shadow:0 2px 6px rgba(0,0,0,.2)}
  .thumb div{width:100%;height:100%}
  .thumb-1{left:92px}.thumb-1 div{background:linear-gradient(180deg,#c9cfd6,#8a9199 60%,#4f8fb0)}
  .thumb-2{left:436px}.thumb-2 div{background:linear-gradient(180deg,#5d86b8,#b9c7d8 55%,#e5e8ec)}
  .thumb-3{left:780px}.thumb-3 div{background:linear-gradient(180deg,#9aa6b3,#d6dde4 60%,#5c6470)}
  .services{position:absolute;left:92px;top:722px;padding-left:33px;border-left:6px solid var(--green);
    font-family:"Montserrat",Arial,sans-serif;font-weight:900;font-size:42px;line-height:52px;
    text-transform:uppercase;color:var(--ink);letter-spacing:-.3px}
  .details{position:absolute;left:87px;top:842px;width:606px;height:399px;background:var(--panel);
    border-radius:6px 0 0 6px;padding:30px 20px 0 30px;box-shadow:0 4px 12px rgba(0,0,0,.12)}
  .details li{list-style:none;position:relative;padding-left:32px;font-size:20px;line-height:26.5px;margin-bottom:17px}
  .details li svg,.perks li svg{position:absolute;left:0;top:4px}
  .perks{position:absolute;left:692px;top:842px;width:403px;height:399px;border-radius:6px;
    background:linear-gradient(135deg,var(--green-light),var(--green));padding:26px 18px 0 22px;
    font-family:"Poppins",Arial,sans-serif;font-weight:600;color:var(--white);font-size:27px;line-height:33px}
  .perks li{list-style:none;position:relative;padding-left:33px;white-space:nowrap}
  .perks li + li{border-top:2px solid rgba(255,255,255,.7);margin-top:18px;padding-top:18px}
  .perks li + li svg{top:22px}
  .accent-line{position:absolute;left:0;top:1269px;width:1183px;height:9px;
    background:linear-gradient(90deg,var(--green-light),var(--yellow))}
  .footer{position:absolute;left:0;top:1278px;width:1183px;height:253px;background:var(--footer);color:var(--white)}
  .address{position:absolute;left:117px;top:40px;font-family:"Poppins",Arial,sans-serif;font-weight:500;font-size:23px;line-height:29px}
  .address svg{position:absolute;left:-30px;top:2px}
  .phone{position:absolute;left:87px;top:108px;width:370px;height:46px;background:var(--yellow);border-radius:23px;
    font-family:"Montserrat",Arial,sans-serif;font-weight:800;font-size:38px;line-height:46px;color:var(--ink);padding-left:62px}
  .phone-icon{position:absolute;left:-2px;top:-3px;width:52px;height:52px;border-radius:50%;background:var(--green);border:3px solid var(--white)}
  .email{position:absolute;left:117px;top:173px;font-family:"Poppins",Arial,sans-serif;font-weight:500;font-size:23px}
  .email svg{position:absolute;left:-32px;top:9px}
  .brand{position:absolute;left:640px;top:80px;display:flex;align-items:center;gap:14px;
    font-family:"Montserrat",Arial,sans-serif;font-weight:800;font-size:40px;color:var(--green-light)}
  .brand-dot{width:26px;height:26px;border-radius:50%;background:var(--green-light)}
  .website{position:absolute;left:665px;top:173px;font-family:"Montserrat",Arial,sans-serif;font-weight:700;font-size:22px;letter-spacing:5px}
  .website svg{position:absolute;left:-32px;top:4px}
</style>
</head>
<body>
<main class="flyer">
  <section class="hero">
    <div class="worker-photo" role="img" aria-label="Photo of a construction worker in an orange hard hat and overalls"></div>
    <h1 class="headline">
      <span class="lead lead-1">Looking for a</span>
      <span class="big big-career">Career?</span>
      <span class="lead lead-2">Join our</span>
      <span class="big big-boot">boot</span>
      <span class="big big-camp">Camp!</span>
    </h1>
  </section>
  <div class="divider"></div>
  <div class="band"></div>
  <figure class="thumb thumb-1"><div role="img" aria-label="Photo of a finished pool screen enclosure over a pool"></div></figure>
  <figure class="thumb thumb-2"><div role="img" aria-label="Photo of two installers fitting a screen enclosure roof"></div></figure>
  <figure class="thumb thumb-3"><div role="img" aria-label="Photo of a worker installing screen panels"></div></figure>

  <h2 class="services">We design, manufacture and install<br>custom pool screen enclosures.</h2>

  <ul class="details">
    <li><svg width="20" height="20" viewBox="0 0 20 20"><circle cx="10" cy="10" r="8.5" fill="none" stroke="#1f9a3f" stroke-width="1.6"/><path d="M6 10.3l2.8 2.7L14 7.5" fill="none" stroke="#1f9a3f" stroke-width="1.6"/></svg>We have a training program to allow Non Experienced motivated people the chance at a great career that will provide a great living for them and their family.</li>
    <li><svg width="20" height="20" viewBox="0 0 20 20"><circle cx="10" cy="10" r="8.5" fill="none" stroke="#1f9a3f" stroke-width="1.6"/><path d="M6 10.3l2.8 2.7L14 7.5" fill="none" stroke="#1f9a3f" stroke-width="1.6"/></svg>This will be a paid boot camp, week long, we provide all the initial training for them to make a transition into our business.</li>
    <li><svg width="20" height="20" viewBox="0 0 20 20"><circle cx="10" cy="10" r="8.5" fill="none" stroke="#1f9a3f" stroke-width="1.6"/><path d="M6 10.3l2.8 2.7L14 7.5" fill="none" stroke="#1f9a3f" stroke-width="1.6"/></svg>5 days of training with a guaranteed job to start the following Monday</li>
    <li><svg width="20" height="20" viewBox="0 0 20 20"><circle cx="10" cy="10" r="8.5" fill="none" stroke="#1f9a3f" stroke-width="1.6"/><path d="M6 10.3l2.8 2.7L14 7.5" fill="none" stroke="#1f9a3f" stroke-width="1.6"/></svg>This is good for both someone with no construction experience or someone with construction experience that wants to upgrade their current job</li>
  </ul>

  <ul class="perks">
    <li><svg width="20" height="20" viewBox="0 0 20 20"><circle cx="10" cy="10" r="8.5" fill="none" stroke="#fff" stroke-width="1.6"/><path d="M6 10.3l2.8 2.7L14 7.5" fill="none" stroke="#fff" stroke-width="1.6"/></svg>Paid Boot Camp</li>
    <li><svg width="20" height="20" viewBox="0 0 20 20"><circle cx="10" cy="10" r="8.5" fill="none" stroke="#fff" stroke-width="1.6"/><path d="M6 10.3l2.8 2.7L14 7.5" fill="none" stroke="#fff" stroke-width="1.6"/></svg>Transition to a full time<br>job with great pay</li>
    <li><svg width="20" height="20" viewBox="0 0 20 20"><circle cx="10" cy="10" r="8.5" fill="none" stroke="#fff" stroke-width="1.6"/><path d="M6 10.3l2.8 2.7L14 7.5" fill="none" stroke="#fff" stroke-width="1.6"/></svg>Benefits include<br>Health Insurance,<br>Dental and Vision, 401K,<br>we provide<br>the tools and training.</li>
  </ul>

  <div class="accent-line"></div>
  <footer class="footer">
    <p class="address"><svg width="18" height="24" viewBox="0 0 18 24"><circle cx="9" cy="8" r="5.5" fill="none" stroke="#f5bd0a" stroke-width="2"/><path d="M9 13.5V20M3 21h12" stroke="#f5bd0a" stroke-width="2"/></svg>418 Coral Bay Road, Sandport<br>FL 33001</p>
    <p class="phone"><span class="phone-icon"><svg width="46" height="46" viewBox="0 0 46 46"><path d="M16 12c-2 1-3 3-2 6 2 6 7 11 13 14 3 1 5 0 6-2l-4-4-3 2c-3-2-6-5-8-8l2-3z" fill="#fff"/></svg></span>555-014-2290</p>
    <p class="email"><svg width="20" height="14" viewBox="0 0 20 14"><rect x="1" y="1" width="18" height="12" fill="none" stroke="#f5bd0a" stroke-width="1.6"/><path d="M1 1l9 7 9-7" fill="none" stroke="#f5bd0a" stroke-width="1.6"/></svg>hello@harborlinescreens.com</p>
    <div class="brand"><span class="brand-dot"></span>Harborline Screens</div>
    <p class="website"><svg width="22" height="22" viewBox="0 0 22 22"><circle cx="11" cy="11" r="9" fill="none" stroke="#f5bd0a" stroke-width="1.8"/><path d="M2 11h18M11 2c4 4 4 14 0 18M11 2c-4 4-4 14 0 18" fill="none" stroke="#f5bd0a" stroke-width="1.5"/></svg>www.HarborlineScreens.com</p>
  </footer>
</main>
</body>
</html>
```